Interactive Tailored Suit and Shirt Website Needs Homepage Redesign

We need our homepage redesigned. Our current website is dated and we need a refresh. We are a Melbourne based business selling tailored suits and shirts in store and online. The homepage should be fashion forward. Our colour scheme has traditionally been black and white but would interested in new ideas.
Our current website is nimbrelo.com.au

```html
<!DOCTYPE html>
<html lang="en">
<head>
<meta charset="utf-8">
<title>nimbrelo — Tailored Suits &amp; Shirts</title>
<link href="https://fonts.googleapis.com/css2?family=Questrial&family=Roboto+Condensed:wght@300;400&family=Open+Sans:wght@400;600&display=swap" rel="stylesheet">
<style>
  :root {
    --bar-dark: #262626;
    --bar-line: #303030;
    --text-light: #e8e8e8;
    --text-muted: #a9a9a9;
    --accent: rgba(204, 82, 90, 0.88);
    --accent-deep: rgba(190, 64, 72, 0.95);
    --accent-solid: #cf5760;
    --social: #555555;
    --white: #ffffff;
  }
  * { margin: 0; padding: 0; box-sizing: border-box; }
  a { text-decoration: none; color: inherit; outline: none; }
  html, body { width: 1200px; height: 817px; overflow: hidden; background: var(--bar-dark); }
  .page { position: relative; width: 1200px; height: 817px; overflow: hidden; font-family: "Roboto Condensed", sans-serif; }

  .site-header {
    position: absolute; left: 0; top: 0; width: 1200px; height: 88px;
    background: repeating-linear-gradient(0deg, var(--bar-dark) 0 2px, var(--bar-line) 2px 3px);
  }
  .brand { position: absolute; left: 180px; top: 26px; font-family: "Questrial", sans-serif; font-size: 27px; color: var(--white); letter-spacing: 0.3px; }
  .main-nav a {
    position: absolute; top: 35px; font-size: 15px; font-weight: 300; color: var(--text-light); letter-spacing: 0.2px;
  }
  .phone { position: absolute; left: 898px; top: 32px; display: flex; align-items: center; gap: 6px; color: var(--text-light); font-size: 15px; font-weight: 300; }

  .hero { position: absolute; left: 0; top: 88px; width: 1200px; height: 641px; }
  .hero-photo { position: absolute; top: 0; height: 641px; }
  .hero-photo.suit { left: 0; width: 600px; background: linear-gradient(90deg, #c9c9c9 0%, #e9e9e9 15%, #3a3a3a 35%, #242424 60%, #d8d8d8 100%); }
  .hero-photo.shirt { left: 600px; width: 600px; background: linear-gradient(90deg, #b8b2a8 0%, #5e6f83 30%, #243a5c 50%, #b59c7a 75%, #d4d0c8 100%); }

  .tagline span {
    position: absolute; height: 46px; width: 223px; padding-left: 27px; background: var(--accent);
    color: var(--white); font-size: 37px; font-weight: 300; line-height: 46px; text-align: left;
    letter-spacing: -1.5px; white-space: nowrap; overflow: hidden;
  }
  .tagline .line-1 { left: 486px; top: 169px; }
  .tagline .line-2 { left: 537px; top: 221px; padding-left: 35px; }
  .tagline .line-3 { left: 486px; top: 272px; }

  .category-bar { position: absolute; left: 293px; top: 426px; width: 640px; height: 127px; background: var(--accent); }
  .click-tab {
    position: absolute; top: 0; width: 71px; height: 127px; background: var(--accent-deep);
    display: flex; align-items: center; justify-content: center; color: var(--white);
  }
  .click-tab span { transform: rotate(-90deg); white-space: nowrap; color: var(--white); font-size: 21px; font-weight: 300; }
  .click-tab.left { left: 0; }
  .click-tab.right { right: 0; }
  .category {
    position: absolute; top: 0; height: 127px; line-height: 127px; color: var(--white);
    font-size: 84px; font-weight: 300; letter-spacing: -1px; white-space: nowrap;
    transform: scaleX(0.88); transform-origin: left center;
  }
  .category.suits { left: 104px; }
  .category.shirts { left: 340px; }

  .newsletter-tab {
    position: absolute; left: 1160px; top: 168px; width: 40px; height: 185px; background: var(--accent-solid);
    display: flex; align-items: center; justify-content: center;
  }
  .newsletter-tab span { transform: rotate(-90deg); white-space: nowrap; color: var(--white); font-size: 16px; font-weight: 300; }

  .site-footer {
    position: absolute; left: 0; top: 729px; width: 1200px; height: 88px;
    background: repeating-linear-gradient(0deg, var(--bar-dark) 0 2px, var(--bar-line) 2px 3px);
  }
  .footer-nav a {
    position: absolute; top: 25px; font-family: "Open Sans", sans-serif; font-size: 9px; color: var(--text-muted); text-transform: uppercase;
  }
  .copyright { position: absolute; left: 184px; top: 52px; font-family: "Open Sans", sans-serif; font-size: 8.5px; color: var(--text-muted); }
  .social { position: absolute; left: 888px; top: 28px; }
</style>
</head>
<body>
<div class="page">
  <header class="site-header">
    <div class="brand">nimbrelo</div>
    <nav class="main-nav">
      <a href="#" style="left:396px">CUSTOMIZE YOUR OWN</a>
      <a href="#" style="left:595px">LOOK BOOK</a>
      <a href="#" style="left:720px">MY NIMBRELO</a>
    </nav>
    <div class="phone">
      <svg width="14" height="22" viewBox="0 0 14 22" aria-hidden="true">
        <rect x="1" y="1" width="12" height="20" rx="1.5" fill="none" stroke="#9a9a9a" stroke-width="1.5"/>
        <rect x="3" y="3.5" width="8" height="13" fill="#9a9a9a"/>
        <circle cx="7" cy="18.5" r="1" fill="#9a9a9a"/>
      </svg>
      <span>+613 9000 4821</span>
    </div>
  </header>

  <section class="hero">
    <div class="hero-photo suit" role="img" aria-label="Photograph of a man in a tailored black suit with white shirt and navy tie, standing against a pale wall"></div>
    <div class="hero-photo shirt" role="img" aria-label="Photograph of a man in a navy shirt and beige trousers leaning on a stone wall in a city street"></div>

    <div class="tagline">
      <span class="line-1">YOUR DESIGN</span>
      <span class="line-2">PERFECT FIT</span>
      <span class="line-3">GUARANTEED</span>
    </div>

    <div class="category-bar">
      <a class="click-tab left" href="#"><span>CLICK HERE</span></a>
      <div class="category suits">SUITS</div>
      <div class="category shirts">SHIRTS</div>
      <a class="click-tab right" href="#"><span>CLICK HERE</span></a>
    </div>

    <div class="newsletter-tab"><span>NEWSLETTER SIGNUP</span></div>
  </section>

  <footer class="site-footer">
    <nav class="footer-nav">
      <a href="#" style="left:184px">Home</a>
      <a href="#" style="left:237px">Customize your own</a>
      <a href="#" style="left:359px">Lookbook</a>
      <a href="#" style="left:441px">About nimbrelo</a>
      <a href="#" style="left:539px">My nimbrelo</a>
      <a href="#" style="left:638px">FAQ</a>
      <a href="#" style="left:681px">T&amp;C</a>
      <a href="#" style="left:730px">Contact us</a>
    </nav>
    <div class="copyright">© 2012-2013 NIMBRELO. ALL RIGHT RESERVED.</div>
    <svg class="social" width="130" height="30" viewBox="0 0 130 30" aria-hidden="true">
      <circle cx="14" cy="15" r="13.5" fill="var(--social)"/>
      <circle cx="49" cy="15" r="13.5" fill="var(--social)"/>
      <circle cx="82" cy="15" r="13.5" fill="var(--social)"/>
      <circle cx="115" cy="15" r="13.5" fill="var(--social)"/>
    </svg>
  </footer>
</div>
</body>
</html>
```